Velvet Dice Night Age Verification Landing Page

To create a visually appealing design for the landing page of the adult game "Velvet Dice Night" that confirms the visitor's age.
The design should have a simple and visually appealing look that focuses on two buttons labeled "Yes" and "No". The purpose of the page is to confirm that the visitor is 18 years of age or older before accessing the game's content. Responsive design that works well on desktop and mobile devices. The final output should be delivered in PSD, AI, or Sketch format, along with any necessary images or assets.
I have also attached examples.

```html
<!DOCTYPE html>
<html lang="en">
<head>
<meta charset="UTF-8">
<title>Velvet Dice Night – Age Verification</title>
<link href="https://fonts.googleapis.com/css2?family=Cinzel:wght@500&family=Lexend:wght@400;500&display=swap" rel="stylesheet">
<style>
  :root {
    --crimson: #d10f58;
    --ink: #151515;
    --white: #ffffff;
    --panel: rgba(255, 255, 255, 0.26);
    --icon-bg: #1c2733;
  }
  * { margin: 0; padding: 0; box-sizing: border-box; }
  html, body { width: 1200px; height: 547px; overflow: hidden; }
  body { font-family: "Lexend", "Helvetica Neue", Arial, sans-serif; }

  .stage {
    position: relative;
    width: 1200px;
    height: 547px;
    overflow: hidden;
  }
  .backdrop {
    position: absolute;
    inset: 0;
    background:
      radial-gradient(ellipse 220px 180px at 130px 330px, rgba(190, 110, 140, 0.55), transparent 70%),
      radial-gradient(ellipse 260px 150px at 420px 470px, rgba(150, 40, 60, 0.55), transparent 70%),
      radial-gradient(ellipse 160px 240px at 960px 300px, rgba(225, 215, 220, 0.6), transparent 70%),
      radial-gradient(ellipse 180px 140px at 1100px 370px, rgba(120, 30, 40, 0.5), transparent 70%),
      linear-gradient(90deg, #6d6258 0%, #8f8379 25%, #b9b3ad 45%, #9a938d 65%, #5d5550 85%, #3e3936 100%);
  }
  .backdrop::after {
    content: "";
    position: absolute;
    inset: 0;
    background: linear-gradient(180deg, rgba(255,255,255,0.05) 0%, rgba(40,40,60,0.25) 100%);
  }

  .music-toggle {
    position: absolute;
    left: 1061px;
    top: 19px;
    width: 40px;
    height: 40px;
    background: var(--icon-bg);
    border: 2px solid var(--crimson);
    display: flex;
    align-items: center;
    justify-content: center;
  }

  .age-panel {
    position: absolute;
    left: 334px;
    top: 95px;
    width: 532px;
    height: 356px;
    border-radius: 14px;
    background: var(--panel);
  }
  .brand-ring {
    position: absolute;
    left: 201px;
    top: 36px;
    width: 98px;
    height: 98px;
    border: 1.5px solid var(--crimson);
    border-radius: 50%;
  }
  .brand-name {
    position: absolute;
    left: 0;
    right: 0;
    top: 156px;
    text-align: center;
    font-family: "Cinzel", Georgia, serif;
    font-weight: 500;
    font-size: 31px;
    color: var(--ink);
    letter-spacing: 0.5px;
  }
  .age-question {
    position: absolute;
    left: 0;
    right: 0;
    top: 216px;
    text-align: center;
    font-size: 19px;
    font-weight: 400;
    color: var(--white);
    letter-spacing: 0.3px;
  }
  .choice {
    position: absolute;
    top: 254px;
    height: 42px;
    background: var(--crimson);
    color: var(--white);
    font-size: 17px;
    font-weight: 500;
    display: flex;
    align-items: center;
    justify-content: center;
  }
  .choice--yes { left: 206px; width: 54px; }
  .choice--no { left: 271px; width: 53px; }
  .remember {
    position: absolute;
    left: 208px;
    top: 309px;
    display: flex;
    align-items: center;
    gap: 12px;
    font-size: 13px;
    color: var(--white);
  }
  .remember-box {
    width: 9px;
    height: 9px;
    background: var(--white);
  }
</style>
</head>
<body>
<main class="stage">
  <div class="backdrop" role="img" aria-label="Blurred photo of friends relaxing together on a sofa at home"></div>

  <div class="music-toggle" aria-label="Toggle music">
    <svg width="24" height="24" viewBox="0 0 24 24" fill="#ffffff">
      <path d="M8 4 L20 2 V16.5 A3 3 0 1 1 18 13.8 V6.2 L10 7.5 V18.5 A3 3 0 1 1 8 15.8 Z"/>
    </svg>
  </div>

  <section class="age-panel">
    <div class="brand-ring"></div>
    <h1 class="brand-name">Velvet Dice Night</h1>
    <p class="age-question">Are You Over 18 years of Age?</p>
    <div class="choice choice--yes">Yes</div>
    <div class="choice choice--no">No</div>
    <label class="remember"><span class="remember-box"></span>Remember Me</label>
  </section>
</main>
</body>
</html>
```